Falkrin homes and renovations business card design.

Would like some new card designs utilizing my new logo that look professional. I am open to different colors on the logo or utilize the same ones we have. I like the original concept but would like to see some fresh ideas and build on what we have already done.

Target Market(s)

Custom home building industry, Real estate sales, Renovation projects.

Industry/Entity Type

Home Builder

Contact Information for Business Card

Falkrin Homes and Renovations
2871 96th Avenue
Marlow Ridge, Westland
T2R3W8
Home : 403- 718-4063 Cell: 403- 294-5170

My info is : Dax Falkrin, President and CEO
email: falkrinhomes@maildrop-example.net
Website: falkrinhomes-example.com
websit

Requirements
Must have
• Must Use my new logo design. I am open to different colors on the logo or utilize the same ones in the existing design. I can upload the original logo design if needed.

```html
<!DOCTYPE html>
<html lang="en">
<head>
<meta charset="utf-8">
<title>Falkrin Homes and Renovations – Business Card</title>
<link rel="stylesheet" href="https://fonts.googleapis.com/css2?family=Open+Sans:wght@400;600;700&display=swap">
<style>
  :root {
    --backdrop-light: #e4e4e6;
    --backdrop-dark: #b9b9bc;
    --card-black: #0c0c0c;
    --card-black-soft: #1c1c1c;
    --card-white: #ffffff;
    --gold: #b8913a;
    --gold-bright: #f2b705;
    --text-light: #f2f2f2;
  }
  * { box-sizing: border-box; margin: 0; padding: 0; }
  html, body {
    width: 1200px; height: 1200px; overflow: hidden;
  }
  body {
    background: radial-gradient(circle at 50% 40%, var(--backdrop-light), var(--backdrop-dark));
    font-family: "Open Sans", Arial, sans-serif;
    position: relative;
  }
  .card {
    position: absolute;
    left: 150px;
    width: 900px;
    height: 514px;
    border-radius: 30px;
    overflow: hidden;
    box-shadow: 0 18px 40px rgba(0,0,0,0.28);
  }
  .card--front {
    top: 60px;
    background: radial-gradient(circle at 50% 45%, var(--card-black-soft), var(--card-black) 70%);
  }
  .card--back {
    top: 626px;
    background: var(--card-white);
  }
  .brand {
    position: absolute;
    display: flex;
    align-items: center;
    gap: 16px;
    color: var(--gold);
    font-weight: 700;
    font-size: 40px;
    line-height: 1.15;
    letter-spacing: 0.5px;
  }
  .brand__mark {
    width: 22px; height: 22px;
    background: var(--gold);
    flex: none;
  }
  .card--front .brand {
    left: 50%; top: 190px;
    transform: translateX(-50%);
    white-space: nowrap;
  }
  .front-website {
    position: absolute;
    left: 0; right: 0; bottom: 70px;
    text-align: center;
    color: var(--gold-bright);
    font-size: 22px;
    letter-spacing: 1.5px;
  }
  .back-panel {
    position: absolute; inset: 0;
    width: 900px; height: 514px;
  }
  .card--back .brand {
    left: 60px; top: 205px;
    width: 330px;
    font-size: 34px;
  }
  .contact {
    position: absolute;
    left: 540px; top: 110px;
    color: var(--text-light);
    font-size: 17px;
    line-height: 1.45;
  }
  .contact__name {
    color: var(--gold-bright);
    font-weight: 700;
    font-size: 25px;
    line-height: 1.2;
  }
  .contact__title { margin-bottom: 18px; }
  .contact__address { margin-bottom: 18px; }
  .contact__list { list-style: none; }
  .contact__list li {
    display: flex; align-items: center; gap: 10px;
  }
  .contact__icon {
    width: 15px; height: 15px; flex: none;
    fill: var(--gold-bright);
  }
</style>
</head>
<body>

  <section class="card card--front" aria-label="Card front">
    <div class="brand"><span class="brand__mark"></span>Falkrin Homes and Renovations</div>
    <p class="front-website">falkrinhomes-example.com</p>
  </section>

  <section class="card card--back" aria-label="Card back">
    <svg class="back-panel" viewBox="0 0 900 514" aria-hidden="true">
      <path d="M360,0 C372,120 470,170 505,290 C525,370 520,450 505,514 L900,514 L900,0 Z" fill="var(--card-black)"/>
      <path d="M360,0 C372,120 470,170 505,290 C525,370 520,450 505,514" fill="none" stroke="var(--gold)" stroke-width="5"/>
    </svg>

    <div class="brand"><span class="brand__mark"></span>Falkrin Homes and Renovations</div>

    <div class="contact">
      <p class="contact__name">Dax Falkrin</p>
      <p class="contact__title">President &amp;CEO</p>
      <p class="contact__address">2871 96th Avenue<br>Marlow Ridge, Westland, T2R3W8</p>
      <ul class="contact__list">
        <li>
          <svg class="contact__icon" viewBox="0 0 24 24"><path d="M6.6 10.8a15 15 0 0 0 6.6 6.6l2.2-2.2c.3-.3.7-.4 1-.2 1.1.4 2.3.6 3.6.6.6 0 1 .4 1 1V20c0 .6-.4 1-1 1A17 17 0 0 1 3 4c0-.6.4-1 1-1h3.5c.6 0 1 .4 1 1 0 1.3.2 2.5.6 3.6.1.3 0 .7-.2 1z"/></svg>
          403- 718-4063
        </li>
        <li>
          <svg class="contact__icon" viewBox="0 0 24 24"><path d="M7 1h10a2 2 0 0 1 2 2v18a2 2 0 0 1-2 2H7a2 2 0 0 1-2-2V3a2 2 0 0 1 2-2zm0 3v14h10V4zm5 15.5a1 1 0 1 0 0 2 1 1 0 0 0 0-2z"/></svg>
          403- 294-5170
        </li>
        <li>
          <svg class="contact__icon" viewBox="0 0 24 24"><path d="M2 5h20v14H2zm2 2v.5l8 5 8-5V7l-8 5z"/></svg>
          falkrinhomes@maildrop-example.net
        </li>
        <li>
          <svg class="contact__icon" viewBox="0 0 24 24"><path d="M12 2a10 10 0 1 0 0 20 10 10 0 0 0 0-20zm6.9 6h-3a15 15 0 0 0-1.3-3.9A8 8 0 0 1 18.9 8zM12 4c.8 1.2 1.5 2.5 1.9 4h-3.8c.4-1.5 1.1-2.8 1.9-4zM4.3 14a8 8 0 0 1 0-4h3.4a16 16 0 0 0 0 4zm.8 2h3a15 15 0 0 0 1.3 3.9A8 8 0 0 1 5.1 16zm3-8h-3a8 8 0 0 1 4.3-3.9A15 15 0 0 0 8.1 8zM12 20c-.8-1.2-1.5-2.5-1.9-4h3.8c-.4 1.5-1.1 2.8-1.9 4zm2.3-6H9.7a14 14 0 0 1 0-4h4.6a14 14 0 0 1 0 4zm.3 5.9a15 15 0 0 0 1.3-3.9h3a8 8 0 0 1-4.3 3.9zm1.7-5.9a16 16 0 0 0 0-4h3.4a8 8 0 0 1 0 4z"/></svg>
          falkrinhomes-example.com
        </li>
      </ul>
    </div>
  </section>

</body>
</html>
```